Real Estate 2015 sold listings postcard

Real estate. I want one side to list 2015 sales. Mailing side with additional information. I am including a "concept" but it needs to be professionalized... Feel free to change color, fonts, layout, add watermark, whatever you think will work. Text on backside may be tweaked. I do want postcards addressed. How do i send mailing list or does Kestro mail do that part?

NOTE: Postcard should be 8.5 x 5.5 inches.
Updates

postcard should be 8.5" x 5.5" size

Target Market(s)

Home owners who may want to sell

Industry/Entity Type

Real Estate Agent

Requirements
Must have
• The sold information and contact oinformation I have provided
Nice to have
• Watermark with my initials

```html
<!DOCTYPE html>
<html lang="en">
<head>
<meta charset="utf-8">
<title>Seller Postcard – Dana Whitfield</title>
<link rel="stylesheet" href="https://fonts.googleapis.com/css2?family=Lato:ital,wght@0,300;0,400;0,700;0,900;1,400&display=swap">
<style>
:root{
  --red:#e2323c;
  --red-deep:#b3222b;
  --red-dark:#8f1a21;
  --wine:#8e1b22;
  --gold:#d7a300;
  --ink:#2a2a2a;
  --white:#ffffff;
  --bg-grey:#e4e4e4;
}
*{margin:0;padding:0;box-sizing:border-box}
html,body{width:1200px;height:777px;overflow:hidden;background:#fff}
.postcard{
  position:relative;width:1200px;height:777px;overflow:hidden;
  font-family:"Lato",sans-serif;color:var(--ink);
  background:linear-gradient(100deg,var(--bg-grey) 0%,#f4f4f4 40%,#fff 65%);
  border:1px solid #555;
}
.header-art{position:absolute;left:0;top:0}
.headline{position:absolute;left:30px;top:22px;color:var(--white);font-weight:300;line-height:1}
.headline .line1{font-size:54px}
.headline .line2{font-size:44px;margin-top:12px}
.headline .line3{font-size:44px;margin-top:14px}
.headline b{font-weight:900}
.agent-photo{position:absolute;left:606px;top:48px;width:156px;height:156px;border-radius:50%;
  border:3px solid #fff;background:radial-gradient(circle at 50% 40%,#c98c6a 0%,#8b3a2e 45%,#3a4a3a 100%)}
.agent-info{position:absolute;left:760px;top:0;width:200px;height:240px;text-align:center}
.agent-info > *{position:absolute;left:0;right:0;line-height:1}
.agent-name{top:68px;color:#fff;font-weight:700;font-size:22px;letter-spacing:.3px}
.agent-license{top:103px;color:#f6dcdc;font-weight:300;font-size:15px}
.agent-phone{top:150px;color:var(--wine);font-weight:300;font-size:28px;letter-spacing:.5px}
.agent-email{top:185px;color:var(--wine);font-size:17px}
.agent-web{top:209px;left:10px;right:10px;background:var(--gold);color:#fff;font-weight:700;
  font-size:16px;padding:3px 0;border-radius:12px}
.tab-offers{position:absolute;left:106px;top:218px;color:var(--wine);font-weight:900;font-size:34px}
.tab-prices{position:absolute;left:148px;top:289px;color:#fff;font-weight:900;font-size:34px}
.reach{position:absolute;color:var(--wine);font-weight:700;font-size:24px}
.reach.one{left:38px;top:340px}
.reach.two{left:96px;top:377px}
.cta-banner{position:absolute;left:0;top:398px}
.cta-text{position:absolute;left:28px;top:419px;white-space:nowrap}
.cta-text .wait{color:var(--wine);font-weight:300;font-size:35px}
.cta-text .call{color:#fff;font-weight:900;font-size:27px}
.body-copy{position:absolute;left:30px;top:475px;width:752px;font-size:18px;line-height:24px;text-align:justify}
.body-copy p+p{margin-top:7px}
.disclaimer{position:absolute;left:30px;top:714px;color:var(--red-deep);font-style:italic;font-size:17px}
.mail-area{position:absolute;left:801px;top:340px;width:388px;height:422px;border:1px solid #333;background:#fff}
.mail-area .divider{position:absolute;left:0;right:0;top:335px;border-top:1px solid #333}
.mail-extension{position:absolute;left:519px;top:676px;width:283px;height:86px;border:1px solid #333;border-right:none;background:#fff}
</style>
</head>
<body>
<div class="postcard">
  <svg class="header-art" width="1200" height="360" viewBox="0 0 1200 360" aria-hidden="true">
    <defs>
      <linearGradient id="redSweep" x1="0" y1="0" x2="1" y2="0">
        <stop offset="0" stop-color="#d92a33"/>
        <stop offset=".45" stop-color="#e8404a"/>
        <stop offset="1" stop-color="#d2262f"/>
      </linearGradient>
    </defs>
    <path d="M0 0H1012V192C1005 150 985 126 870 124C830 120 790 120 760 124C700 132 650 142 600 158C470 240 380 252 300 262C200 275 80 262 0 228Z" fill="url(#redSweep)"/>
    <path d="M762 97C850 86 960 98 1012 125V192C1005 150 985 126 870 124C830 120 790 120 762 124Z" fill="var(--red-dark)"/>
    <path d="M114 250H390V322Q390 336 376 336H128Q114 336 114 322Z" fill="var(--red-deep)"/>
    <path d="M30 260C60 240 80 210 110 205H280C300 205 320 240 350 252C250 275 120 275 30 260Z" fill="#fff"/>
    <path d="M40 262C140 288 280 285 400 258C500 235 560 190 620 165" fill="none" stroke="var(--red-deep)" stroke-width="4"/>
  </svg>

  <div class="headline">
    <div class="line1">Traditionally</div>
    <div class="line2"><b>FEB</b> through <b>APRIL</b></div>
    <div class="line3">are the <b>best months to sell</b></div>
  </div>

  <div class="agent-photo" role="img" aria-label="Portrait photo of the agent"></div>
  <div class="agent-info">
    <div class="agent-name">DANA WHITFIELD</div>
    <div class="agent-license">License : #00481357</div>
    <div class="agent-phone">555-318-0427</div>
    <div class="agent-email">dwhitfield@harborlane.com</div>
    <div class="agent-web">www.dwhitfield.com</div>
  </div>

  <div class="tab-offers">Most Offers</div>
  <div class="tab-prices">Highest Prices</div>

  <div class="reach one">Our Listings are advertised</div>
  <div class="reach two">Locally and in more than 30 countries!!</div>

  <svg class="cta-banner" width="720" height="66" viewBox="0 0 720 66" aria-hidden="true">
    <path d="M650 0H708L682 24L708 48H676V16Z" fill="var(--gold)"/>
    <path d="M650 0L676 16H650Z" fill="#9c7a10"/>
    <rect x="0" y="16" width="676" height="48" fill="var(--gold)"/>
  </svg>
  <div class="cta-text"><span class="wait">Don't Wait...</span> <span class="call">Call Now for a Private Consultation!</span></div>

  <div class="body-copy">
    <p>Our market continues to be strong, which reflects both our vibrant and growing local economy and our seemingly chronic shortage of inventory. As long as those conditions continue, our market values will remain high. That is good news to sellers who may want to down-size or move to a different area for a new job, or maybe to be closer to family.</p>
    <p>As a certified Harbor Lane Relocation Specialist, I can connect you with experienced and professional real estate agent anywhere in the country and in most countries around the world. We can co-ordinate your transactions at both ends, making your transition as seamless as possible. If you are planning a move, across the street or across the county, call me now for a confidential consultation.</p>
  </div>
  <div class="disclaimer">If your home is already listed, this is not meant as a solicitation.</div>

  <div class="mail-extension"></div>
  <div class="mail-area"><div class="divider"></div></div>
</div>
</body>
</html>
```